Cruise Booking Website

Cruise search and booking website

This project is a redesign of a cruise booking website we did a few years ago.

The current website is located here: http://voyage.pylonworks.example/en/

It's not fully functional but gives you ad idea how miserable the old design was.

All the information about cruises, cruise lines, destinations, ports and shore excursions will be similar to http://www.sailquest.example/
Actual search pages (form, results, single result, sailing and cabin selection, ship info, booking) will have EXACTLY the same info as sailquest.example

We like the style of http://harborfleetdesk.example, it's quite modern, good spacing, not overloaded with information. So you can use it as an example of what we like, not what we want as a final result for us. Please, don't copy it. The result should not be possible to resemble the harborfleetdesk.example, because our site has to be unique. This is important!
If you submit a design that clearly reminds another cruise site it will be rejected!

Also the mockup provided is just to give you the basic structure and show what information has to be present on the page. It doesn't mean the layout has to be the same as a mockup. The layout is up to the designer.

I've updated the mockup to be more generic so it doesn't confuse you:
https://files.boxvault.example/s/k7m2qp9wz4hx/Home%20page.png

When you're adding social sharing icons like plazanet/chirpline you have to use chinese ones instead:
https://files.boxvault.example/s/t3nr8vx5lc2e/chinese-social-icons.png
Originals: http://minilk.example/qR7t

We'll start with home page first and after it's approved inner pages can be designed.

I know the cost of the project doesn't look high, but the task is straight forward and doesn't require to be very original, it's better to follow existing design and layout patterns that proved to work well.
That's why I encourage you to choose a template to build the design on top of one of https://themeparlor.example/ themes if it will save the design work, will be easier and faster for you. So it will be more like a customization than a new design from scratch.

Mockups, site map and logo files:
- https://files.boxvault.example/sh/h48dm2rs73fkpw/QvnbW2Xz8e

Website tree:
- https://sheets.papernest.example/document/d/7xPqR2mLw9sTk4VbN8cHj3YzA6eUf5GdKo1iMnBv/edit?usp=sharing
Updates

So far a lot of designs are just copying http://www.harborfleetdesk.example/ - we don't like it!

We like the style of harborfleetdesk.example, it's quite modern, good spacing, not overloaded with information. So you can use it as an example of what we like, not what we want as a final result for us. Please, don't copy it. The result should not be possible to resemble the harborfleetdesk.example, because our site has to be unique. This is important!

Target Market(s)

Chinese travellers

Industry/Entity Type

Build

Requirements
Must have
• * White, blue and red
* Large spacing, not too much information cramped into a small space like sailquest.example or the current website
* More "hidden" info in popups, tabs and so on, so not to many things are visible at the same time
* Compatible with kestrel scaffold styling (for easier coding):
- http://kestrelkit.codeshelf.example/scaffold/index.html
- http://skinmarket.example/
* Feel free to propose to build the design on top of one of https://themeparlor.example/ themes if it will save the design work, will be easier and faster for you

```html
<!DOCTYPE html>
<html lang="en">
<head>
<meta charset="utf-8">
<title>Haiyun Cruises — Home</title>
<link rel="stylesheet" href="https://fonts.googleapis.com/css2?family=Source+Sans+3:ital,wght@0,400;0,600;0,700;1,600;1,700&family=Noto+Sans+SC:wght@700&display=swap">
<style>
:root{
  --bg-deep:#1f5f98;
  --bg-light:#e4f0fa;
  --brand:#1f6bb0;
  --nav-line:#0f6db3;
  --ink:#333;
  --orange-dark:#f26a00;
  --panel:rgba(30,30,30,.9);
  --footer:#3f78ad;
  --footer-bar:#35679a;
  --tab:#5d5d5d;
  --tab-active:#6cc3ec;
  --check:#58b22c;
}
*{box-sizing:border-box;margin:0;padding:0}
html,body{width:1161px;height:1200px;overflow:hidden}
body{
  font-family:"Source Sans 3",sans-serif;color:var(--ink);
  background:radial-gradient(ellipse 520px 900px at 50% 45%,var(--bg-light) 0%,#8fbfe4 45%,var(--bg-deep) 100%);
  position:relative;
}
.page{position:absolute;left:174px;top:0;width:813px;height:1200px;background:#fff;box-shadow:0 0 18px rgba(0,0,0,.25)}
.abs{position:absolute}

/* header */
.logo{left:12px;top:34px;display:flex;align-items:center;gap:8px;font-family:"Source Sans 3","Noto Sans SC",sans-serif;font-weight:700;font-size:31px;color:var(--brand)}
.logo-dot{width:44px;height:44px;border-radius:50%;background:var(--brand)}
.account{left:594px;top:19px;font-size:11px;color:var(--brand)}
.account span{margin:0 6px}
.social{left:699px;top:16px;display:flex;gap:4px}
.social i{width:22px;height:22px;border-radius:4px;display:block}
.search{left:440px;top:62px;width:191px;height:22px;border:1px solid #ccc;border-radius:2px;background:#f4f4f4;font-size:8px;color:#777;padding:6px 9px;display:flex;justify-content:space-between}
.hotline{left:655px;top:58px;display:flex;gap:8px;align-items:center}
.hotline-num{font-size:19px;font-weight:700;color:var(--brand);line-height:1}
.hotline-sub{font-size:14px;color:#333;line-height:1.3}

/* nav */
.nav{left:0;top:108px;width:813px;height:33px;background:linear-gradient(#1a8ad6,#0f72bf);display:flex}
.nav a{height:33px;display:flex;align-items:center;justify-content:center;color:#fff;font-size:10.5px;font-weight:700;text-decoration:none;border-right:1px solid var(--nav-line)}
.nav a.active{background:linear-gradient(#3aacee,#1d8fd8)}

/* hero */
.hero{left:0;top:141px;width:813px;height:415px;overflow:hidden;
  background:
    radial-gradient(ellipse 420px 120px at 55% 30%,rgba(255,255,255,.55),rgba(255,255,255,0) 70%),
    linear-gradient(180deg,#7fb3df 0%,#a9cfec 18%,#d6e7f1 34%,#a8bfc6 42%,#7e9c86 50%,#5f8a55 62%,#4f7a3f 74%,#7a6f66 86%,#8f7a74 100%)}
.hero-tag{left:334px;top:142px;color:var(--brand);font-style:italic;font-weight:700;letter-spacing:-.8px}
.hero-tag .l1{font-size:25px;line-height:1.25;font-weight:600}
.hero-tag .l2{font-size:31px;line-height:1.2}
.finder{left:558px;top:36px;width:239px;height:339px;background:var(--panel);border-radius:3px;color:#eee}
.finder h2{position:absolute;left:21px;top:15px;font-size:22px;font-weight:400;color:#fff}
.finder hr{position:absolute;left:0;top:46px;width:239px;border:0;border-top:2px solid #555}
.finder .lbl{position:absolute;font-size:11.5px;color:#eee}
.finder .big{font-size:13px}
.sel{position:absolute;height:21px;background:linear-gradient(#f5f5f5,#dcdcdc);border-radius:2px;font-size:9px;color:#333;padding:5px 9px}
.sel::after{content:"";position:absolute;right:0;top:0;width:18px;height:21px;border-left:1px solid #bbb}
.sel b{position:absolute;right:6px;top:5px;width:0;height:0;border:3px solid transparent;border-bottom-color:#777}
.sel b+b{top:12px;border-bottom-color:transparent;border-top-color:#777}
.senior{position:absolute;left:20px;top:266px;font-size:9px;display:flex;align-items:center;gap:4px}
.senior i{width:10px;height:10px;background:#ddd;border-radius:2px;display:block}
.btn-search{position:absolute;left:19px;top:287px;width:202px;height:32px;background:linear-gradient(#ffab1e,var(--orange-dark));border-radius:2px;color:#fff;font-size:15px;font-weight:600;display:flex;align-items:center;justify-content:center}
.dots{left:750px;top:383px;display:flex;gap:3px}
.dots i{width:10px;height:10px;border-radius:50%;background:#fff;display:block}

/* tabs */
.tabs{left:13px;top:574px;height:31px;display:flex}
.tab{height:31px;background:var(--tab);color:#e5e5e5;font-size:11px;display:flex;align-items:center;padding-left:20px;clip-path:polygon(0 0,88% 0,100% 100%,0 100%);margin-right:-4px}
.tab.active{background:linear-gradient(#8fd2f2,var(--tab-active));color:#1b5a8c}
.book{left:13px;top:605px;width:601px;height:250px;border:1px solid #ddd}
.book-photo{left:19px;top:26px;width:306px;height:195px;border:4px solid #ddd;
  background:linear-gradient(180deg,#c2e2f5 0%,#8fcbec 22%,#3aa8d8 36%,#1f93c8 55%,#1786bd 72%,#5aa3c8 80%,#eef2f4 86%,#dfe6ea 100%)}
.book-title{left:350px;top:26px;font-size:26px;font-weight:700;color:var(--brand)}
.book-sub{left:350px;top:58px;font-size:15.5px;color:#444}
.book-lead{left:350px;top:84px;font-size:15px;color:var(--brand);line-height:1.25;width:240px}
.checks{left:350px;top:134px;list-style:none;font-size:9.5px;color:#444}
.checks li{height:22px;display:flex;align-items:center;gap:6px}

/* sidebar */
.news-photo{left:639px;top:574px;width:154px;height:131px;
  background:
    radial-gradient(ellipse 60px 28px at 70% 52%,rgba(255,255,255,.85),rgba(255,255,255,0) 75%),
    linear-gradient(180deg,#6f9fc8 0%,#9ec0dc 22%,#3f74a6 32%,#24588c 60%,#163f6d 100%)}
.news-title{left:639px;top:718px;font-size:13px;font-weight:700;color:var(--brand)}
.news-text{left:639px;top:741px;font-size:12.5px;color:var(--brand);line-height:1.5;width:165px}
.email{left:638px;top:790px;width:159px;height:22px;border:1px solid #ccc;border-radius:2px;background:#f5f5f5;font-size:9px;color:#777;padding:5px 9px}
.btn-sub{left:638px;top:824px;width:85px;height:22px;background:linear-gradient(#ff7a1a,#e83e00);border-radius:2px;color:#fff;font-size:9.5px;display:flex;align-items:center;justify-content:center}

/* partners */
.partners-title{left:14px;top:880px;font-size:15px;font-weight:700;color:var(--brand)}
.arrows{left:759px;top:882px;display:flex;gap:2px}
.arrows i{width:17px;height:17px;background:#ddd;display:flex;align-items:center;justify-content:center}
.partner{top:911px;width:120px;height:60px;border:1px solid #ddd;display:flex;align-items:center;justify-content:center;gap:6px}
.partner i{display:block}

/* footer */
.footer{left:0;top:974px;width:813px;height:185px;background:var(--footer);color:#fff}
.footer-bar{left:0;top:1159px;width:813px;height:41px;background:var(--footer-bar);color:#fff;font-size:8.5px;display:flex;align-items:center;justify-content:center}
.f-title{position:absolute;font-size:13.5px;font-weight:700}
.f-links{position:absolute;list-style:none;font-size:9px}
.f-links li{height:18.2px}
.f-logo{position:absolute;left:336px;top:62px;width:82px;height:80px;background:#fff;display:flex;flex-direction:column;align-items:center;justify-content:center;gap:5px;font-family:"Source Sans 3","Noto Sans SC",sans-serif;font-weight:700;font-size:11px;color:var(--brand)}
.f-logo i{width:30px;height:30px;border-radius:50%;background:var(--brand);display:block}
.f-about{position:absolute;left:435px;top:68px;font-size:10.5px;line-height:15px;width:100px}
.f-contact{position:absolute;left:585px;top:54px;font-size:11px;line-height:16px}
.f-line{position:absolute;left:585px;font-size:10.5px;display:flex;align-items:center;gap:5px}
</style>
</head>
<body>
<div class="page">

  <header>
    <div class="abs logo"><span class="logo-dot"></span>海韵 Haiyun</div>
    <div class="abs account">Sign in<span>|</span>Signup</div>
    <div class="abs social" aria-label="Social links">
      <i style="background:#e6322b"></i><i style="background:#3fa9e0"></i><i style="background:#f08a00"></i><i style="background:#d9362b"></i>
    </div>
    <div class="abs search">SEARCH :
      <svg width="10" height="10" viewBox="0 0 10 10"><circle cx="4" cy="4" r="3" fill="none" stroke="#aaa" stroke-width="1.2"/><line x1="6.3" y1="6.3" x2="9" y2="9" stroke="#aaa" stroke-width="1.2"/></svg>
    </div>
    <div class="abs hotline">
      <svg width="30" height="30" viewBox="0 0 30 30"><circle cx="15" cy="15" r="13.5" fill="none" stroke="#999" stroke-width="1.5"/><path d="M11 8c-2 1-2 4 0 8s5 7 8 7c1 0 2-1 2-2l-3-2-2 1c-1-1-3-3-4-5l1-2-2-5z" fill="#888"/></svg>
      <div><div class="hotline-num">400 512 808</div><div class="hotline-sub">Call Us Today!</div></div>
    </div>
  </header>

  <nav class="abs nav">
    <a class="active" style="width:84px">HOME</a>
    <a style="width:117px">DESTINATIONS</a>
    <a style="width:104px">CRUISE LINES</a>
    <a style="width:106px">CRUISE INFO</a>
    <a style="width:79px">DEALS</a>
    <a style="width:128px">ONLINE BOOKING</a>
    <a style="width:102px">CONTACT US</a>
    <a style="width:93px;border-right:0">BLOG</a>
  </nav>

  <section class="abs hero" role="img" aria-label="Hikers on a mountain summit photographing a coastal valley">
    <div class="abs hero-tag"><div class="l1">Cruise Vacations</div><div class="l2">&amp; So much more...</div></div>
    <form class="abs finder">
      <h2>Find Your Cruise</h2><hr>
      <span class="lbl" style="left:20px;top:56px">Destination</span>
      <div class="sel" style="left:20px;top:73px;width:197px">Destination name<b></b><b></b></div>
      <span class="lbl" style="left:20px;top:100px">Length</span>
      <span class="lbl" style="left:127px;top:100px">Month</span>
      <div class="sel" style="left:20px;top:118px;width:89px">Length Area</div>
      <div class="sel" style="left:127px;top:118px;width:89px"><b></b><b></b></div>
      <span class="lbl" style="left:18px;top:147px">Cruise Lines</span>
      <div class="sel" style="left:18px;top:164px;width:200px">Any Cruise line<b></b><b></b></div>
      <span class="lbl big" style="left:18px;top:196px">Number of Travelers</span>
      <span class="lbl" style="left:20px;top:218px">Age 25+</span>
      <span class="lbl" style="left:127px;top:218px">Age 0 to 24</span>
      <div class="sel" style="left:19px;top:236px;width:90px">5<b></b><b></b></div>
      <div class="sel" style="left:127px;top:236px;width:89px">0<b></b><b></b></div>
      <div class="senior"><i></i>Check for senior rates</div>
      <div class="btn-search">Search Cruises</div>
    </form>
    <div class="abs dots"><i></i><i></i><i></i></div>
  </section>

  <div class="abs tabs">
    <div class="tab active" style="width:122px">BOOK WITH US</div>
    <div class="tab" style="width:91px;padding-left:26px">DEALS</div>
    <div class="tab" style="width:108px;padding-left:30px">PACKAGES</div>
    <div class="tab" style="width:84px;padding-left:26px">NEWS</div>
    <div class="tab" style="width:161px;padding-left:26px">FIRST TIME CRUISER?</div>
  </div>

  <section class="abs book">
    <div class="abs book-photo" role="img" aria-label="Couple sitting on a seawall looking out over a turquoise sea"></div>
    <h1 class="abs book-title">BOOK WITH US!</h1>
    <p class="abs book-sub">It's easy and Fun</p>
    <p class="abs book-lead">We're most advanced cruise book-ing provider in china</p>
    <ul class="abs checks">
      <li><svg width="11" height="9" viewBox="0 0 11 9"><path d="M1 5l3 3 6-7" fill="none" stroke="#58b22c" stroke-width="2"/></svg>Great prices</li>
      <li><svg width="11" height="9" viewBox="0 0 11 9"><path d="M1 5l3 3 6-7" fill="none" stroke="#58b22c" stroke-width="2"/></svg>Fast booking processing</li>
      <li><svg width="11" height="9" viewBox="0 0 11 9"><path d="M1 5l3 3 6-7" fill="none" stroke="#58b22c" stroke-width="2"/></svg>20 Cruise Lines</li>
      <li><svg width="11" height="9" viewBox="0 0 11 9"><path d="M1 5l3 3 6-7" fill="none" stroke="#58b22c" stroke-width="2"/></svg>Destinations around the world</li>
    </ul>
  </section>

  <aside>
    <div class="abs news-photo" role="img" aria-label="White cruise ship sailing on deep blue water"></div>
    <h3 class="abs news-title">Cruise Deals Newsletter</h3>
    <p class="abs news-text">Subscribe to the best deals Now!</p>
    <div class="abs email">Email :</div>
    <div class="abs btn-sub">Subscribe</div>
  </aside>

  <section>
    <h3 class="abs partners-title">OUR RELIABLE PARTNERS</h3>
    <div class="abs arrows">
      <i><svg width="7" height="9"><path d="M5 1L2 4.5 5 8" fill="none" stroke="#888" stroke-width="1.4"/></svg></i>
      <i><svg width="7" height="9"><path d="M2 1l3 3.5L2 8" fill="none" stroke="#888" stroke-width="1.4"/></svg></i>
    </div>
    <div class="abs partner" style="left:16px"><i style="width:16px;height:16px;background:#d8433a"></i><i style="width:64px;height:12px;background:#e9c7c4;border-radius:2px"></i></div>
    <div class="abs partner" style="left:149px"><i style="width:16px;height:16px;background:#f2b21c;border-radius:50%"></i><i style="width:64px;height:12px;background:#c4d4ea;border-radius:2px"></i></div>
    <div class="abs partner" style="left:281px"><i style="width:16px;height:16px;background:#4c5b6b"></i><i style="width:64px;height:10px;background:#d6dbe0;border-radius:2px"></i></div>
    <div class="abs partner" style="left:414px"><i style="width:60px;height:12px;background:#f8d9a0;border-radius:2px"></i></div>
    <div class="abs partner" style="left:547px"><i style="width:26px;height:26px;background:#7fc4e8;border-radius:50%"></i></div>
    <div class="abs partner" style="left:680px"><i style="width:28px;height:28px;background:#3d93d3;border-radius:50%"></i><i style="width:44px;height:10px;background:#cfe2f2;border-radius:2px"></i></div>
  </section>

  <footer class="abs footer">
    <h4 class="f-title" style="left:27px;top:26px">Useful Pages</h4>
    <ul class="f-links" style="left:27px;top:51px">
      <li>About Us</li><li>Contact us</li><li>Blog</li><li>FAQ</li><li>Terms of Service</li><li>Payment info</li><li>Reward Points</li>
    </ul>
    <h4 class="f-title" style="left:184px;top:26px">Cruise Infov</h4>
    <ul class="f-links" style="left:185px;top:50px">
      <li>Cruise news</li><li>Visa</li><li>Honeymoon cruises</li><li>Firsttime on a Cruise</li>
    </ul>
    <h4 class="f-title" style="left:336px;top:30px">About haiyuncruise.example</h4>
    <div class="f-logo"><i></i>海韵 Haiyun</div>
    <p class="f-about">We're the most advanced cruise booking providr in china.</p>
    <h4 class="f-title" style="left:585px;top:30px">Contact Us</h4>
    <p class="f-contact">Tidewell Studio Ltd<br>Harbourview block 18, Quay Road 2<br>Portmere 20418 Coastland</p>
    <div class="f-line" style="top:110px"><svg width="12" height="9" viewBox="0 0 12 9"><path d="M1 3c2-2 8-2 10 0l-2 1.5c-1-.5-5-.5-6 0zM3 4h6l1 4H2z" fill="#fff"/></svg>(210) 555-0142 - (210) 555-0187</div>
    <div class="f-line" style="top:131px"><svg width="12" height="9" viewBox="0 0 12 9"><rect x=".5" y=".5" width="11" height="8" fill="#fff"/><path d="M.5 .5l5.5 4.5 5.5-4.5" fill="none" stroke="#3f78ad"/></svg>hello@haiyuncruise.example</div>
  </footer>
  <div class="abs footer-bar">© 2013. haiyuncruise. All rights reserved.</div>

</div>
</body>
</html>
```